Looking for a modern, Professional business card design

We have a simple business card, but are looking for a more modern, professional look. A sample of the basic card is attached as well as the logo. We would also like to add that we offer:
Struggling with your finances?
- Learn to become debt free
- Discover the power of cash
- Control your money instead of it controlling you
Let us help you achieve a new level of financial freedom!
Also, we would like to have a "SPECIAL OFFER!: FREE 30 minute consultation"
Financial Planning

```html
<!DOCTYPE html>
<html lang="en">
<head>
<meta charset="utf-8">
<title>Northpath Money Coaching – Business Card</title>
<link rel="stylesheet" href="https://fonts.googleapis.com/css2?family=Arimo:wght@400;700&display=swap">
<style>
  :root {
    --stage: #3b3b3d;
    --card-white: #ffffff;
    --card-black: #0c0c0c;
    --green: #5aa82c;
    --green-light: #8cc63f;
    --ink: #222222;
    --ink-soft: #555555;
    --band-dark: #2a2a2a;
    --white-soft: #e8e8e8;
  }
  * { box-sizing: border-box; margin: 0; padding: 0; }
  html, body { width: 1200px; height: 950px; overflow: hidden; }
  body {
    background: var(--stage);
    font-family: "Arimo", Arial, sans-serif;
    display: flex;
    flex-direction: column;
    align-items: center;
    justify-content: center;
    gap: 50px;
  }
  .card {
    width: 700px;
    height: 400px;
    position: relative;
    overflow: hidden;
    box-shadow: 0 10px 30px rgba(0,0,0,.45);
  }

  /* Back */
  .card--back {
    background: linear-gradient(160deg, #1d1d1d 0%, var(--card-black) 55%, #000 100%);
    color: var(--white-soft);
    padding: 56px 60px;
  }
  .brand { display: flex; align-items: center; gap: 16px; }
  .brand__dot { width: 46px; height: 46px; border-radius: 50%; flex: none; }
  .brand__name { font-weight: 700; font-size: 34px; line-height: 1; letter-spacing: .5px; }
  .brand__tagline { font-size: 13px; margin-top: 8px; }
  .card--back .brand__dot { background: var(--white-soft); }
  .card--back .brand__name { color: var(--white-soft); }
  .card--back .brand__tagline { color: #bdbdbd; margin-left: 62px; }
  .pitch { margin-top: 40px; }
  .pitch__head { font-weight: 700; font-size: 21px; letter-spacing: .5px; margin-bottom: 12px; }
  .pitch__list { font-size: 17px; line-height: 1.5; }
  .pitch__close { font-size: 17px; margin-top: 4px; }
  .pitch__offer { font-weight: 700; font-size: 19px; margin-top: 18px; color: var(--green-light); }

  /* Front */
  .card--front { background: var(--card-white); }
  .card--front .brand { position: absolute; top: 84px; right: 50px; }
  .card--front .brand__dot { background: var(--green); }
  .card--front .brand__name { color: var(--ink); font-size: 32px; }
  .card--front .brand__tagline { position: absolute; top: 140px; right: 50px; color: var(--green); }
  .contact { position: absolute; left: 52px; top: 150px; }
  .contact__name { color: var(--green); font-weight: 700; font-size: 27px; }
  .contact__role { color: var(--ink); font-size: 20px; margin-top: 4px; }
  .contact__list { list-style: none; margin-top: 16px; }
  .contact__item { display: flex; align-items: center; gap: 12px; font-size: 19px; color: var(--ink-soft); line-height: 1.55; }
  .contact__item svg { width: 18px; height: 18px; flex: none; }
  .band { position: absolute; left: 0; right: 0; bottom: 0; height: 30px; display: flex; }
  .band__green { width: 58%; background: linear-gradient(90deg, var(--green) 0%, var(--green-light) 100%); }
  .band__dark { flex: 1; background: var(--band-dark); }
</style>
</head>
<body>

<section class="card card--back" aria-label="Business card back">
  <div class="brand">
    <span class="brand__dot"></span>
    <span class="brand__name">Northpath Money Coaching</span>
  </div>
  <p class="brand__tagline">Achieve a new level of personal freedom</p>
  <div class="pitch">
    <p class="pitch__head">STRUGGLING WITH YOUR FINANCES?</p>
    <p class="pitch__list">Learn to become debt free • Discover the power of cash<br>• Control your money instead of it controlling you</p>
    <p class="pitch__close">Let us help you achieve a new level of financial freedom!</p>
    <p class="pitch__offer">SPECIAL OFFER! FREE 30 minute consultation</p>
  </div>
</section>

<section class="card card--front" aria-label="Business card front">
  <div class="brand">
    <span class="brand__dot"></span>
    <span class="brand__name">Northpath Money Coaching</span>
  </div>
  <p class="brand__tagline">Achieve a new level of personal freedom</p>

  <div class="contact">
    <p class="contact__name">Daniel R. Hayes</p>
    <p class="contact__role">Personal Financial Coach</p>
    <ul class="contact__list">
      <li class="contact__item">
        <svg viewBox="0 0 18 18" aria-hidden="true"><rect x="4" y="1" width="10" height="16" rx="2" fill="none" stroke="#5aa82c" stroke-width="2"/><circle cx="9" cy="14" r="1" fill="#5aa82c"/></svg>
        (205) 555-0187
      </li>
      <li class="contact__item">
        <svg viewBox="0 0 18 18" aria-hidden="true"><rect x="1" y="4" width="16" height="11" fill="#5aa82c"/><path d="M1 4 L9 10 L17 4" fill="none" stroke="#fff" stroke-width="1.5"/></svg>
        daniel@steadyledgercoach.com
      </li>
      <li class="contact__item">
        <svg viewBox="0 0 18 18" aria-hidden="true"><circle cx="9" cy="9" r="8" fill="#5aa82c"/><path d="M1 9h16M9 1c3 3 3 13 0 16M9 1c-3 3-3 13 0 16" fill="none" stroke="#fff" stroke-width="1"/></svg>
        www.steadyledgercoach.com
      </li>
    </ul>
  </div>

  <div class="band">
    <span class="band__green"></span>
    <span class="band__dark"></span>
  </div>
</section>

</body>
</html>
```